Redesign of business card for Cedar Ridge Mechanical

We are looking for a new design for our business cards for Cedar Ridge Mechanical. We are a plumbing & HVAC construction company, operating on the West Coast of Canada and USA. Logo attached.
Industry/Entity Type
Construction - Plumbing & HVAC
Contact Information for Business Card
Name, address, phone numbers, email, website address
Look and feel
Each slider illustrates characteristics of the customer's brand and the style your logo design should communicate.

```html
<!DOCTYPE html>
<html lang="en">
<head>
<meta charset="UTF-8">
<title>Cedar Ridge Mechanical – Business Card</title>
<link href="https://fonts.googleapis.com/css2?family=Montserrat:wght@400;500;700&display=swap" rel="stylesheet">
<style>
  :root {
    --canvas: #ececec;
    --card-light: #ffffff;
    --card-dark: #050505;
    --ink: #111111;
    --ink-soft: #2a2a2a;
    --paper: #ffffff;
  }
  * { box-sizing: border-box; margin: 0; padding: 0; }
  html, body {
    width: 1200px;
    height: 780px;
    overflow: hidden;
  }
  body {
    background: var(--canvas);
    font-family: "Montserrat", sans-serif;
    display: flex;
    align-items: center;
    justify-content: center;
    gap: 40px;
  }
  .card {
    width: 520px;
    height: 300px;
    border-radius: 24px;
    position: relative;
    flex: none;
    box-shadow: 0 10px 28px rgba(0,0,0,0.18);
  }
  .card--front { background: var(--card-light); color: var(--ink); }
  .card--back {
    background: var(--card-dark);
    color: var(--paper);
    display: flex;
    align-items: center;
    justify-content: center;
    gap: 18px;
  }

  .details {
    position: absolute;
    left: 50px;
    top: 86px;
    display: flex;
    align-items: flex-start;
    gap: 18px;
  }
  .identity { white-space: nowrap; }
  .identity__name {
    font-weight: 700;
    font-size: 21px;
    letter-spacing: 0.4px;
    text-transform: uppercase;
    line-height: 1.2;
  }
  .identity__title {
    font-weight: 400;
    font-size: 14px;
    color: var(--ink-soft);
    margin-top: 3px;
  }
  .divider {
    flex: none;
    width: 2px;
    height: 70px;
    margin-top: 34px;
    background: var(--ink);
  }
  .contacts {
    list-style: none;
    font-size: 14px;
    font-weight: 400;
    line-height: 1;
    margin-top: 44px;
    white-space: nowrap;
  }
  .contacts__item {
    display: flex;
    align-items: center;
    gap: 8px;
    margin-bottom: 9px;
  }
  .contacts__icon { width: 12px; height: 12px; flex: none; }
  .address {
    position: absolute;
    left: 50px;
    bottom: 56px;
    font-size: 14px;
    font-weight: 400;
  }

  .brand__mark {
    width: 22px;
    height: 22px;
    background: var(--paper);
  }
  .brand__name {
    font-weight: 500;
    font-size: 24px;
    letter-spacing: 1.5px;
    text-transform: uppercase;
  }
</style>
</head>
<body>
  <section class="card card--front">
    <div class="details">
      <div class="identity">
        <p class="identity__name">Daniel Whitford</p>
        <p class="identity__title">Managing Director</p>
      </div>
      <span class="divider"></span>
      <ul class="contacts">
        <li class="contacts__item">
          <svg class="contacts__icon" viewBox="0 0 16 16" aria-hidden="true"><path fill="currentColor" d="M3 1l3 3-1.6 2a9 9 0 0 0 5.6 5.6L12 10l3 3-2 2C7 15 1 9 1 3z"/></svg>
          <span>123 456 789</span>
        </li>
        <li class="contacts__item">
          <svg class="contacts__icon" viewBox="0 0 16 16" aria-hidden="true"><rect x="1" y="3" width="14" height="10" rx="1" fill="currentColor"/><path d="M1.5 3.5L8 9l6.5-5.5" fill="none" stroke="#fff" stroke-width="1.3"/></svg>
          <span>info@yourmail.com</span>
        </li>
        <li class="contacts__item">
          <svg class="contacts__icon" viewBox="0 0 16 16" aria-hidden="true"><circle cx="8" cy="8" r="7" fill="currentColor"/><path d="M1 8h14M8 1c-3 3.5-3 10.5 0 14M8 1c3 3.5 3 10.5 0 14" fill="none" stroke="#fff" stroke-width="1"/></svg>
          <span>www.yourwebsite.com</span>
        </li>
      </ul>
    </div>
    <p class="address">Your address, City State, Zip 1234</p>
  </section>

  <section class="card card--back">
    <span class="brand__mark"></span>
    <p class="brand__name">Cedar Ridge Mechanical</p>
  </section>
</body>
</html>
```